Detail Shop Business card design

i need a business card design for my new detailing company called 'Brisk's Polish Works'. i want an all black and white design . simple, direct and to the point. i want the designer to choose a fitting font to match the logothe front should have logo, address, phone and email and the back side should have a slogan and text indicating that we offer services on anything including cars, trucks, motorcycles and RVs. slogan will read "we take pride in your ride"
maybe also very small on the back side the IG icon with Brisks_Polish_Works

phone 208.417.6352
address 3847 E Larkin Ave
Boise ID 83714
email: BrisksPolish@mailvexo.com

Target Market(s)

all ages , auto enthusiasts

Industry/Entity Type

Automotive

Contact Information for Business Card

the front should have logo, address, phone and email and the back side should have a slogan and text indicating that we offer services on anything including cars, trucks, motorcycles and RVs. slogan will read "we take pride in your ride"

phone 208.417.6352
address 3847 E Larkin Ave
Boise ID 83714

Colors
000000
ffffff

Requirements
Must have
• bold font and very simple design with good spacing
Nice to have
• anything creative from the designer indicating we service any types of vehicles
Should not have
• any colors ,

```html
<!DOCTYPE html>
<html lang="en">
<head>
<meta charset="utf-8">
<title>Brisk's Polish Works – Business Card</title>
<link rel="stylesheet" href="https://fonts.googleapis.com/css2?family=Oswald:wght@700&family=Roboto:wght@400;500&family=Roboto+Condensed:wght@400;700&display=swap">
<style>
  :root {
    --ink: #000000;
    --paper: #ffffff;
    --card-white: #f4f4f4;
    --stage: #e6e6e6;
  }
  * { margin: 0; padding: 0; box-sizing: border-box; }
  html, body { width: 1200px; height: 960px; overflow: hidden; }
  body { background: var(--stage); position: relative; font-family: "Roboto", sans-serif; }

  .card {
    position: absolute;
    width: 600px;
    height: 343px;
    background: var(--card-white);
    box-shadow: 0 2px 6px rgba(0,0,0,0.25);
    overflow: hidden;
  }
  .card--front { left: 314px; top: 113px; }
  .card--back  { left: 311px; top: 472px; }

  /* Front */
  .front__panel {
    position: absolute; left: 297px; top: 0;
    width: 303px; height: 100%;
    background: var(--ink);
    color: var(--paper);
  }
  .front__badge {
    position: absolute; left: 244px; top: 31px;
    width: 72px; height: 72px; border-radius: 50%;
    background: var(--paper);
    border: 4px solid var(--ink);
  }
  .brand {
    position: absolute; left: 60px; top: 116px; width: 200px;
    text-align: center;
    font-family: "Oswald", sans-serif; font-weight: 700;
    font-size: 30px; line-height: 1.1; letter-spacing: 1px;
    color: var(--ink); text-transform: uppercase;
  }
  .person { position: absolute; left: 63px; top: 57px; }
  .person__name {
    font-family: "Roboto Condensed", sans-serif; font-weight: 700;
    font-size: 21px; letter-spacing: 0.3px;
  }
  .person__role {
    font-family: "Roboto Condensed", sans-serif; font-weight: 400;
    font-size: 15px; margin-left: 4px; margin-top: 1px;
  }
  .address {
    position: absolute; left: 63px; top: 164px;
    font-size: 14px; line-height: 18px;
  }
  .contacts { position: absolute; left: 63px; top: 211px; list-style: none; }
  .contacts li {
    display: flex; align-items: center; gap: 8px;
    font-size: 14px; line-height: 19px;
  }
  .contacts svg { width: 13px; height: 13px; fill: var(--paper); flex: none; }

  /* Back */
  .vehicle-art {
    position: absolute; left: 114px; top: 90px;
    width: 380px; height: 135px;
    background: linear-gradient(180deg, #1a1a1a 0%, #3a3a3a 60%, #111 100%);
    border-radius: 40px 40px 6px 6px;
  }
  .slogan {
    position: absolute; left: 0; top: 271px; width: 100%;
    text-align: center;
    font-family: "Roboto", sans-serif; font-weight: 500;
    font-size: 17px; letter-spacing: 0.4px; color: var(--ink);
  }
  .slogan__rule {
    position: absolute; left: 136px; top: 294px;
    width: 326px; height: 1px; background: var(--ink);
  }
  .services {
    position: absolute; left: 0; top: 299px; width: 100%;
    text-align: center;
    font-family: "Roboto Condensed", sans-serif; font-weight: 700;
    font-size: 12.5px; color: var(--ink);
  }
</style>
</head>
<body>

<section class="card card--front" aria-label="Business card front">
  <div class="brand">Brisk's<br>Polish<br>Works</div>
  <div class="front__panel">
    <div class="person">
      <div class="person__name">DALE HARMON</div>
      <div class="person__role">CEO/FOUNDER</div>
    </div>
    <div class="address">3847 E Larkin Ave<br>Boise ID 83714</div>
    <ul class="contacts">
      <li><svg viewBox="0 0 16 16" aria-hidden="true"><path d="M3.5 1l3 3-1.6 2c.8 1.8 2.3 3.3 4.1 4.1l2-1.6 3 3-2 2.5C6.5 13.5 2.5 9.5 1 3.5z"/></svg>208.417.6352</li>
      <li><svg viewBox="0 0 16 16" aria-hidden="true"><path d="M4 0h8a1 1 0 0 1 1 1v14a1 1 0 0 1-1 1H4a1 1 0 0 1-1-1V1a1 1 0 0 1 1-1zm1 2v10h6V2zm3 11a1 1 0 1 0 0 2 1 1 0 0 0 0-2z"/></svg>471 905 2283</li>
      <li><svg viewBox="0 0 16 16" aria-hidden="true"><path d="M1 3h14v10H1zm1.5 1.2V5l5.5 4 5.5-4v-.8L8 8z"/></svg>BrisksPolish@mailvexo.com</li>
      <li><svg viewBox="0 0 16 16" aria-hidden="true"><path d="M8 1a7 7 0 1 0 0 14A7 7 0 0 0 8 1zm0 1.5c.8 0 1.8 1.9 2 4.5H6c.2-2.6 1.2-4.5 2-4.5zM2.6 7h2c.1-1.7.5-3.2 1.1-4.1A5.5 5.5 0 0 0 2.6 7zm0 2a5.5 5.5 0 0 0 3.1 4.1C5.1 12.2 4.7 10.7 4.6 9zm3.4 0h4c-.2 2.6-1.2 4.5-2 4.5S6.2 11.6 6 9zm5.4 0c-.1 1.7-.5 3.2-1.1 4.1A5.5 5.5 0 0 0 13.4 9zm2-2a5.5 5.5 0 0 0-3.1-4.1c.6.9 1 2.4 1.1 4.1z"/></svg>www.briskspolish.com</li>
    </ul>
  </div>
  <div class="front__badge" aria-hidden="true"></div>
</section>

<section class="card card--back" aria-label="Business card back">
  <div class="vehicle-art" role="img" aria-label="Black and white illustration of a vintage hot rod car in side view"></div>
  <div class="slogan">WE TAKE PRIDE IN YOUR RIDE</div>
  <div class="slogan__rule" aria-hidden="true"></div>
  <div class="services">we offer services on anything including cars, trucks, motorcycles &amp; RVs</div>
</section>

</body>
</html>
```